Pinecrest Capital Group - Company Envelopes

I am looking for a graphic designer to create a bespoke envelope for my company use, which I can then have printed at scale. The envelope should be of standard size and shape, but Matt black in colour, with semi-thick vertical gloss (shiny) lines going from left to right, but must stop to the right of the envelope, leaving a Matt black line with enough space for a stamp in the top right corner. The back of the envelope should be full Matt black.

Requirements
Must have
• Must be as described in brief
Should not have
• No other colours - Just Matt and Gloss Black

```html
<!DOCTYPE html>
<html lang="en">
<head>
<meta charset="utf-8">
<title>Pinecrest Capital Group – Envelope</title>
<link rel="stylesheet" href="https://fonts.googleapis.com/css2?family=Cormorant+Garamond:wght@700&display=swap">
<style>
  :root {
    --matt-black: #0b0b0b;
    --matt-deep: #050505;
    --matt-mid: #151515;
    --gloss-sheen: rgba(255, 255, 255, 0.055);
    --gloss-edge: rgba(255, 255, 255, 0.02);
    --gloss-black-light: #2a2a2a;
    --gloss-black-dark: #0e0e0e;
    --ink-white: #ffffff;
  }
  html, body {
    margin: 0;
    padding: 0;
    width: 1200px;
    height: 863px;
    overflow: hidden;
    background: var(--matt-black);
  }
  .envelope {
    position: relative;
    width: 1200px;
    height: 863px;
    overflow: hidden;
  }
  .envelope__surface {
    position: absolute;
    inset: 0;
    background:
      radial-gradient(ellipse at 35% 40%, var(--matt-mid) 0%, transparent 65%),
      linear-gradient(160deg, #1a1a1a 0%, var(--matt-black) 45%, var(--matt-deep) 100%);
  }
  .envelope__gloss-lines {
    position: absolute;
    top: 0;
    bottom: 0;
    left: 0;
    width: 1010px;
    background: repeating-linear-gradient(
      90deg,
      transparent 0px,
      transparent 26px,
      var(--gloss-edge) 26px,
      var(--gloss-sheen) 33px,
      var(--gloss-edge) 40px,
      transparent 40px,
      transparent 52px
    );
  }
  .brand {
    position: absolute;
    left: 331px;
    top: 672px;
    display: flex;
    align-items: flex-end;
    gap: 19px;
  }
  .brand__mark {
    width: 120px;
    height: 120px;
    flex: none;
    background: linear-gradient(135deg, var(--gloss-black-light) 0%, var(--gloss-black-dark) 55%, #000 100%);
  }
  .brand__name {
    font-family: "Cormorant Garamond", serif;
    font-weight: 700;
    color: var(--ink-white);
    margin: 0;
    line-height: 1;
  }
  .brand__primary {
    display: block;
    font-size: 70px;
    letter-spacing: 1px;
    white-space: nowrap;
  }
  .brand__secondary {
    display: block;
    margin-top: 2px;
    font-size: 27px;
    letter-spacing: 12.5px;
    white-space: nowrap;
  }
</style>
</head>
<body>
  <main class="envelope">
    <div class="envelope__surface" role="img" aria-label="Matt black stone texture background"></div>
    <div class="envelope__gloss-lines"></div>
    <div class="brand">
      <div class="brand__mark"></div>
      <p class="brand__name">
        <span class="brand__primary">PINECREST</span>
        <span class="brand__secondary">CAPITAL GROUP</span>
      </p>
    </div>
  </main>
</body>
</html>
```